Doctors Office Web Design

Name of the business is Lian-Hua Qiu M.D.
We need a web design that is attractive for women that want to see Dr. Lian-Hua Qiu for Obstetrician Gynecology and Pregnancy care. Dr. Qiu earned her degree from Harwell Ridge Medical College of obstetrician gynecology. We want to attract women of child bearing ages to come to our offices for health, education, and pregnancies.

Please visit http://www.drqiucareweb.example/ to help you get a feel for who we are. We will be adding some pictures and logo in the next few days.

We are looking for to have pages for and tabs including
About Us- History, Our Staff, Dr. Qiu
Patient Information- Appointments, E-Prescriptions, Payments Accepted, Insurance
Health- General, Sexual, Mental, Affiliates
Pregnancy- Minimally invasive surgery(our specialty), 4-D Ultra Sound, Hospital Affiliations
Media- News,Pictures, Videos
Locations- Palmetto Office, Larkfield Office

The colors we would like to use are pastel colors, magenta, and plum

Target Market(s)

Women of all ages with an emphasis on 25-65 year olds

Industry/Entity Type

Business

Requirements
Must have
• Needs to include a location for a our videos and pictures that I will submit shortly. We also want a map to our location or atleast a place for one.
Nice to have
• A place for a google map of our office locations.

```html
<!DOCTYPE html>
<html lang="en">
<head>
<meta charset="utf-8">
<title>Lian-Hua Qiu M.D.</title>
<link rel="stylesheet" href="https://fonts.googleapis.com/css2?family=Open+Sans:wght@400&family=Roboto+Condensed:wght@300&family=Yanone+Kaffeesatz:wght@300;400&display=swap">
<style>
:root{
  --pink:#f27aa5;
  --magenta-dark:#c2325e;
  --rose-btn:#e7adaf;
  --tagline:#e8a9ad;
  --cream:#fbeee2;
  --peach:#fcd9c4;
  --nav:#c7a38b;
  --brown:#9b7d64;
  --text:#8c7260;
  --line:#d8c6b6;
}
*{margin:0;padding:0;box-sizing:border-box}
html,body{width:1200px;height:1000px;overflow:hidden}
body{position:relative;background:#fff;font-family:'Open Sans',Verdana,sans-serif}
.abs{position:absolute}
.top-band{left:0;top:0;width:1200px;height:105px;background:linear-gradient(#fbc4d8,var(--pink) 90%)}
.address{top:10px;font-family:'Open Sans',Verdana,sans-serif;font-size:12.5px;line-height:15px;color:#fff;letter-spacing:.3px}
.address.left{right:842px;text-align:right}
.address.right{left:842px}
.title-tab{left:370px;top:0;width:460px;height:125px;background:linear-gradient(#ef7ea8,var(--magenta-dark));box-shadow:0 2px 5px rgba(0,0,0,.35);border-radius:0 0 4px 4px;display:flex;align-items:center;justify-content:center}
.title-tab h1{font-family:'Roboto Condensed',sans-serif;font-weight:300;font-size:58px;color:#fff;letter-spacing:-2px;text-shadow:0 2px 2px rgba(0,0,0,.35);margin-top:-10px}
.tagline{left:370px;top:130px;width:460px;text-align:center;font-family:'Yanone Kaffeesatz',sans-serif;font-size:37px;line-height:40px;color:var(--tagline);letter-spacing:.5px}
.service{height:48px;background:var(--rose-btn);color:#fff;font-family:'Yanone Kaffeesatz',sans-serif;font-weight:300;font-size:33px;line-height:47px;padding:0 9px;border-radius:3px;box-shadow:0 1px 2px rgba(0,0,0,.2)}
.hero-photo{left:410px;top:170px;width:380px;height:243px;background:radial-gradient(ellipse at 50% 60%,#eab7c0,#f6dfe2 60%,#fff 75%)}
.content-bg{left:0;top:413px;width:1200px;height:441px;background:var(--cream)}
.nav{left:230px;top:413px;width:740px;height:43px;background:var(--nav);display:flex;justify-content:center;align-items:center;font-family:'Open Sans',Verdana,sans-serif;font-size:13.5px;color:#fff;border-radius:0 0 3px 3px}
.nav span.sep{margin:0 11px}
.nav-shadow{left:100px;top:411px;width:1000px;height:4px;background:linear-gradient(90deg,transparent,rgba(120,100,90,.35),transparent)}
h2{font-family:Arial,sans-serif;font-weight:normal;font-size:24px;color:var(--brown)}
.copy{font-size:12.5px;line-height:20px;color:var(--text);text-align:justify;letter-spacing:.3px}
.copy a{color:var(--text)}
.divider{left:100px;top:605px;width:655px;height:2px;background:var(--line)}
.quote-mark{font-family:Georgia,serif;font-weight:bold;font-size:40px;color:var(--brown);line-height:1}
.col-shadow{left:779px;top:495px;width:14px;height:345px;background:linear-gradient(90deg,rgba(120,100,90,.18),transparent)}
.staff-box{left:818px;top:532px;width:282px;height:134px;border:1px solid var(--line)}
.staff-photo{left:11px;top:11px;width:100px;height:99px;background:#ececec;border:3px solid #fff;box-shadow:0 0 2px rgba(0,0,0,.2)}
.staff-name{left:120px;top:36px;font-size:14px;color:var(--text);line-height:18px}
.staff-name small{font-size:14px;color:#b39d8c}
.arrow-btn{top:106px;width:20px;height:18px;background:#e9d3a8;border:1px solid #d8bc8b;border-radius:3px;color:#8c7260;font-size:14px;text-align:center;line-height:16px}
.video-box{left:818px;top:697px;width:282px;height:157px;background:#f7c6ab;padding:5px 5px 0}
.video-still{width:272px;height:152px;background:linear-gradient(120deg,#e5ddd6,#cfc6c0 45%,#dcc0d8)}
.footer{left:0;top:854px;width:1200px;height:146px;background:var(--peach)}
.map{top:915px;width:299px;height:90px;background:#e7e1d6;border:3px solid #fff;border-bottom:none;box-shadow:0 0 2px rgba(0,0,0,.15)}
.field{left:755px;width:345px;height:36px;background:#fbe3d3;border:2px solid #fff;border-radius:3px;font-family:Arial,sans-serif;font-size:14px;color:var(--brown);padding:8px 15px}
</style>
</head>
<body>
<div class="abs top-band"></div>
<div class="abs address left">2480 Seabreeze Avenue Suite<br>210-212<br>Larkfield, Florida 33401<br>Tel: (555) 014-2271<br>Fax: (555) 014-2290</div>
<div class="abs address right">780 N.W. 22nd Street<br>Suite 140B<br>Palmetto, Florida 33490<br>Tel: (555) 018-3365<br>Fax: (555) 018-3377</div>
<div class="abs title-tab"><h1>Lian-Hua Qiu M.D.</h1></div>
<div class="abs tagline">Serving All Areas of Women's Health</div>

<div class="abs service" style="left:101px;top:151px">Obstetrics</div>
<div class="abs service" style="left:101px;top:238px">Family Planning</div>
<div class="abs service" style="left:101px;top:331px">Hormonal Evaluation</div>
<div class="abs service" style="left:988px;top:151px">Infertility</div>
<div class="abs service" style="left:945px;top:238px">Incontinence</div>
<div class="abs service" style="left:867px;top:331px">Gynecology Surgery</div>

<div class="abs hero-photo" role="img" aria-label="Photo of two smiling expectant mothers in pink tops"></div>

<div class="abs content-bg"></div>
<div class="abs nav-shadow"></div>
<nav class="abs nav">
  <span>HOME</span><span class="sep">|</span><span>ABOUT US</span><span class="sep">|</span><span>PATIENT INFORMATION</span><span class="sep">|</span><span>HEALTH</span><span class="sep">|</span><span>PREGNANCY</span><span class="sep">|</span><span>MEDIA</span><span class="sep">|</span><span>LOCATIONS</span>
</nav>

<h2 class="abs" style="left:101px;top:490px">Welcome to Dr. Lian-Hua Qiu's Website</h2>
<p class="abs copy" style="left:100px;top:528px;width:656px">Here you will be able to find information about both of our offices, meet Dr. Qiu and her staff, and browse through our women's health links to learn more about pregnancy, nutrition, exercise, and other women's health issues. Have fun and if you have any questions, feel free to <a href="#">contact us</a></p>
<div class="abs divider"></div>

<h2 class="abs" style="left:101px;top:621px">What Our Patient’s Say</h2>
<div class="abs quote-mark" style="left:100px;top:660px">“</div>
<p class="abs copy" style="left:100px;top:681px;width:656px">Lorem Ipsum is simply dummy text of the printing and typesetting industry. Lorem Ipsum has been the industry's standard dummy text ever since the 1500s.<br><br>When an unknown printer took a galley of type and scrambled it to make a type specimen book. It has survived not only five centuries, but also the leap into electronic typesetting, remaining essentially unchanged.</p>
<div class="abs quote-mark" style="left:735px;top:802px">”</div>

<div class="abs col-shadow"></div>

<h2 class="abs" style="left:818px;top:490px">Meet Our Staff</h2>
<div class="abs staff-box">
  <div class="abs staff-photo" role="img" aria-label="Staff portrait placeholder"></div>
  <div class="abs staff-name">Dr. Lian-Hua Qiu<br><small>M.D., FACOG</small></div>
  <div class="abs arrow-btn" style="left:226px">&lt;</div>
  <div class="abs arrow-btn" style="left:251px">&gt;</div>
</div>

<div class="abs video-box">
  <div class="video-still" role="img" aria-label="Video still of a doctor performing an ultrasound on a patient"></div>
  <svg class="abs" style="left:118px;top:55px" width="46" height="50" aria-hidden="true"><path d="M2 2 L44 25 L2 48 Z" fill="#3a3a3a" opacity=".85"/></svg>
</div>

<div class="abs footer"></div>
<h2 class="abs" style="left:99px;top:873px">LOCATION MAP</h2>
<div class="abs map" style="left:100px" role="img" aria-label="Street map of the Larkfield office"></div>
<div class="abs map" style="left:420px" role="img" aria-label="Street map of the Palmetto office"></div>

<h2 class="abs" style="left:754px;top:873px">CONTACT US</h2>
<div class="abs field" style="top:914px">Name</div>
<div class="abs field" style="top:959px">Email</div>
</body>
</html>
```